New Innovative Counselling and psychotherapy Service needs Business Card design

Keep it simple and professional. On one side, just company name and logo (perhaps in all blue) and maybe a tag line.

On other side (all white) my name and Qualifications in centre

Industry/Entity Type

Health And Wellness

Contact Information for Business Card

Dara Whelby
Counsellor & Psychotherapist
BSc (Psychol.), BA, Dip. (Couns. & Psych.), PG.Cert (CBT), FGTrK, ONRE

I will also require Mobile no, Email and web site address of which I'll pass on to final designer.

Font styles to use
Sans Serif

Requirements
Must have
• My Logo Only and please use the colours in logo that is in it.
Should not have
• Any other images

```html
<!DOCTYPE html>
<html lang="en">
<head>
<meta charset="utf-8">
<title>Stillwater Path – Business Card</title>
<link rel="stylesheet" href="https://fonts.googleapis.com/css2?family=Roboto:wght@400;700&family=Roboto+Condensed:wght@400&display=swap">
<style>
  :root {
    --page-bg: #e6e8ea;
    --card-bg: #f6f7f7;
    --sky-blue: #45a9e0;
    --sky-blue-soft: #6bbbe6;
    --leaf-green: #84c44a;
    --ink: #2f3336;
    --name-white: #f3f6f8;
    --title-white: #e4f2fb;
    --icon-teal: #4aa98a;
  }
  * { margin: 0; padding: 0; box-sizing: border-box; }
  html, body {
    width: 1200px; height: 1054px; overflow: hidden;
    background: var(--page-bg);
    font-family: "Roboto", Arial, sans-serif;
  }
  .business-card {
    position: absolute; left: 100px; top: 227px;
    width: 1000px; height: 600px;
    background: var(--card-bg);
    border-radius: 6px;
    overflow: hidden;
    box-shadow: 0 10px 30px rgba(0,0,0,0.12);
  }
  .header-band {
    position: absolute; left: 0; top: 0;
    width: 100%; height: 250px;
    background: linear-gradient(180deg, var(--sky-blue) 0%, var(--sky-blue-soft) 100%);
  }
  .header-rule {
    position: absolute; left: 0; top: 262px;
    width: 100%; height: 8px;
    background: var(--leaf-green);
  }
  .holder {
    position: absolute; right: 50px; top: 40px;
    text-align: right;
  }
  .holder-name {
    font-weight: 700; font-size: 38px; color: var(--name-white);
    letter-spacing: 0.3px; margin-bottom: 12px;
  }
  .holder-titles {
    font-family: "Roboto Condensed", "Arial Narrow", sans-serif;
    font-size: 21px; line-height: 29px; color: var(--title-white);
  }
  .brand {
    position: absolute; left: 60px; top: 470px;
    display: flex; align-items: center; gap: 16px;
  }
  .brand-dot {
    width: 40px; height: 40px; border-radius: 50%;
    background: var(--sky-blue); flex: none;
  }
  .brand-name {
    font-size: 50px; font-weight: 400; color: var(--ink);
    letter-spacing: -0.5px; line-height: 1;
  }
  .contact-list {
    position: absolute; right: 62px; top: 418px;
    list-style: none; text-align: right;
    font-size: 24px; color: var(--ink);
  }
  .contact-list li {
    display: flex; justify-content: flex-end; align-items: center;
    gap: 12px; height: 40px;
  }
  .contact-list svg { width: 22px; height: 22px; flex: none; }
</style>
</head>
<body>
  <main class="business-card">
    <div class="header-band" role="img" aria-label="Decorative blue and green wave band across the top of the card"></div>
    <div class="header-rule" aria-hidden="true"></div>

    <section class="holder">
      <h1 class="holder-name">Dara Whelby</h1>
      <p class="holder-titles">
        Counsellor &amp; Psychotherapist<br>
        BSc (Psychol.), BA, Dip. (Couns.<br>
        &amp; Psych.), PG.Cert (CBT),<br>
        FGTrK, ONRE
      </p>
    </section>

    <div class="brand">
      <span class="brand-dot" aria-hidden="true"></span>
      <p class="brand-name">Stillwater Path</p>
    </div>

    <ul class="contact-list">
      <li>0987 654 3210
        <svg viewBox="0 0 24 24" aria-hidden="true"><path d="M6.6 10.8a15 15 0 0 0 6.6 6.6l2.2-2.2a1 1 0 0 1 1-.25 11.4 11.4 0 0 0 3.6.57 1 1 0 0 1 1 1V20a1 1 0 0 1-1 1A17 17 0 0 1 3 4a1 1 0 0 1 1-1h3.5a1 1 0 0 1 1 1c0 1.25.2 2.45.57 3.57a1 1 0 0 1-.25 1z" fill="var(--icon-teal)"/></svg>
      </li>
      <li>dara.w@StillwaterPath.com
        <svg viewBox="0 0 24 24" aria-hidden="true"><rect x="2" y="5" width="20" height="14" rx="1.5" fill="var(--icon-teal)"/><path d="M3 6.5l9 6.5 9-6.5" fill="none" stroke="#fff" stroke-width="1.6"/></svg>
      </li>
      <li>www.StillwaterPath.com
        <svg viewBox="0 0 24 24" aria-hidden="true"><circle cx="12" cy="12" r="9.5" fill="none" stroke="var(--icon-teal)" stroke-width="2"/><ellipse cx="12" cy="12" rx="4" ry="9.5" fill="none" stroke="var(--icon-teal)" stroke-width="1.6"/><path d="M2.5 12h19M4.5 7h15M4.5 17h15" stroke="var(--icon-teal)" stroke-width="1.4"/></svg>
      </li>
    </ul>
  </main>
</body>
</html>
```